PeakRoamJourneys

1. Can you describe what your company does?

Please find enclosed documents for your reference about our business doing.

2. Who are your target customers for the website?

Company Positioning: A comprehensive supplier of premier international sports travel and high-end event services.
Core Advantage: Exclusive international partnership resources and an Official Ticketing Assurance System.
Service Standard: One-Stop, High-Quality Service Solutions based on the "An once-in-a-lifetime experience" philosophy.

Our target customers for the website:
Mid-to-High-end Sports Enthusiasts
Corporate Clients
Sports Associations
Please kindly find enclosed for more details about our target customers, I think it's very important to make it clear to you.

3. Do you have an existing domain name / website address?

Yes, I have. I just applied for this new domain and it's totally a new website. www.peakroamjourneys.example

4. In addition to a Home Page, which other pages / sections would you like your website to have:
About Us
Contact Us , Office / Mailing Address
Sports Travel Products( Bucket Lists) : Globe Shield, Royal Quartet, Vantara Games, Football, KHL, Golf, Skiing, Hiking,Galas
Reviews/ Unforgettable Moments
FAQs
Any other page / section you would like: Here is the website for your reference, www.lanewander.example
For each of the pages / sections you’d like to have, please provide the text (and images, if available) you would like to include.
Please recommend 2-3 templates to me, and let me know what kind of text I will provide to every web pages.

5. Which of the below are features and functionalities your website will need:
Image Gallery
Videos
Contact Form
Maps
FAQs
6. Please provide the URLs for the social media profiles you'd like to link to the website.

Do you know Bright Lantern App?

Please let me know anything you need, thank you very much!

Have a good day!

Target Market(s)

Travel for the world-wide sports games and make an once-in-a-lifetime experience

Industry/Entity Type

sports and travel industry

Coding

Number of Pages Required

5+ page

Requirements
Must have
• our logo
Nice to have
• On the homepage, I’d like a banner-style section to prominently showcase the latest products.

```html
<!DOCTYPE html>
<html lang="en">
<head>
<meta charset="utf-8">
<title>PeakRoamJourneys — Sports Travel</title>
<link href="https://fonts.googleapis.com/css2?family=Montserrat:wght@400;500;600;700&family=Quicksand:wght@500;600;700&display=swap" rel="stylesheet">
<style>
:root{
  --navy:#0f1f4b;
  --navy-deep:#0b1940;
  --gold:#c9a84c;
  --ink:#1c1c1c;
  --muted:#555;
  --grey-bg:#f6f6f6;
  --cream-bg:#f8f5ee;
  --white:#fff;
}
*{box-sizing:border-box;margin:0;padding:0}
html,body{width:1200px;height:4088px;overflow:hidden}
body{font-family:"Montserrat",sans-serif;color:var(--ink);background:var(--white);position:relative}
.abs{position:absolute}
.gold{color:var(--gold)}
.section-title{font-family:"Quicksand",sans-serif;font-weight:600;font-size:41px;text-align:center;color:#222}
.btn{display:flex;align-items:center;justify-content:center;background:var(--navy);color:var(--gold);font-weight:600;font-size:15px;border-radius:24px;white-space:nowrap}

/* hero */
.hero{position:absolute;left:0;top:0;width:1200px;height:780px}
.nav{position:absolute;left:78px;top:5px;width:1042px;height:68px;background:var(--white);border-radius:34px;box-shadow:0 2px 10px rgba(0,0,0,.12);display:flex;align-items:center;padding:0 22px 0 33px;white-space:nowrap}
.nav-logo{font-weight:700;font-size:24px;color:var(--navy);margin-right:40px}
.nav-links{display:flex;gap:44px;font-size:15px;font-weight:500;color:#222;flex:1}
.nav-links .active{color:var(--gold);font-weight:700}
.nav-quote{background:var(--gold);color:#fff;font-size:14px;font-weight:600;padding:10px 18px;border-radius:22px}
.hero-title{left:108px;top:185px;width:660px;font-family:"Quicksand",sans-serif;font-weight:600;font-size:52px;line-height:64px;color:#111}
.hero-sub{left:110px;top:384px;width:520px;font-size:16px;line-height:29px;font-weight:500;color:#111}
.hero-btn{left:111px;top:462px;width:197px;height:47px}
.play{left:351px;top:448px;width:92px;height:92px;border-radius:50%;background:rgba(230,40,40,.55);display:flex;align-items:center;justify-content:center}
.play span{width:54px;height:54px;border-radius:50%;background:#e41b1b;display:flex;align-items:center;justify-content:center}

/* about */
.about-visual{left:63px;top:890px}
.about-title{left:600px;top:880px;font-family:"Quicksand",sans-serif;font-weight:600;font-size:37px;color:#222;white-space:nowrap}
.about-text{left:600px;top:937px;width:490px;border-left:4px solid #333;padding-left:25px;font-size:12.8px;line-height:25px;color:#444;text-align:justify}
.about-text p+p{margin-top:25px}
.about-btn{left:600px;top:1240px;width:135px;height:46px}

/* products */
.products{left:0;top:1395px;width:1200px;height:498px;background:var(--grey-bg);overflow:hidden}
.products .section-title{margin-top:46px}
.product-card{position:absolute;top:141px;width:246px;height:267px;border-radius:10px;overflow:hidden}
.product-card .label{position:absolute;left:0;bottom:0;width:100%;height:66px;background:rgba(40,40,40,.75);color:#fff;font-weight:600;font-size:20px;display:flex;align-items:center;justify-content:center;white-space:nowrap}
.arrow{position:absolute;top:256px;width:38px;height:38px;border:2px solid #fff;border-radius:50%;display:flex;align-items:center;justify-content:center}

/* reviews */
.reviews{left:0;top:1893px;width:1200px;height:440px;background:var(--navy)}
.reviews .section-title{color:#fff;margin-top:46px}
.review-card{position:absolute;top:157px;width:302px;height:196px;background:#fff;border-radius:4px;text-align:center;padding:50px 10px 0}
.avatar{position:absolute;left:50%;top:-37px;margin-left:-37px;width:74px;height:74px;border-radius:50%;border:4px solid #fff;background:linear-gradient(160deg,#b9a89a,#6c5a50)}
.review-card h3{font-size:16px;font-weight:700;color:#111}
.stars{color:#f0a500;font-size:12px;letter-spacing:2px;margin:4px 0 4px}
.review-card p{font-size:11.5px;line-height:26px;color:#333;white-space:nowrap}

/* faq */
.faq{left:0;top:2333px;width:1200px;height:685px}
.faq .section-title{margin-top:57px}
.faq-item{position:absolute;left:111px;width:978px;height:64px;background:#fff;border-radius:32px;box-shadow:0 3px 12px rgba(0,0,0,.1);display:flex;align-items:center;justify-content:space-between;padding:0 28px 0 33px;font-size:15px;color:#333}
.plus{width:22px;height:22px;border-radius:50%;background:var(--navy);color:#fff;display:flex;align-items:center;justify-content:center;font-size:18px;font-weight:700;line-height:1}
.faq-btn{left:532px;top:565px;width:135px;height:45px}

/* contact */
.contact{left:0;top:3018px;width:1200px;height:648px;background:var(--cream-bg)}
.contact .section-title{margin-top:60px}
.field{position:absolute;background:#fff;font-size:15px;font-weight:500;color:#222;padding:22px 24px;box-shadow:0 1px 4px rgba(0,0,0,.06)}
.submit-btn{left:532px;top:542px;width:135px;height:46px}

/* footer */
.footer{left:0;top:3666px;width:1200px;height:422px;background:var(--navy);color:#fff}
.footer-logo{left:111px;top:92px;font-size:30px;font-weight:500}
.social{position:absolute;top:152px;width:27px;height:27px;border-radius:50%;border:2px solid #fff}
.social.on{background:var(--gold);border-color:var(--gold)}
.footer h4{position:absolute;top:75px;font-size:19px;font-weight:600}
.footer ul{position:absolute;top:119px;list-style:none;font-size:15px}
.footer li{height:34.5px;display:flex;align-items:center;gap:10px}
.contact-row{position:absolute;left:828px;display:flex;gap:16px;font-size:15px;line-height:25px}
.ico{width:32px;height:32px;border-radius:50%;background:#fff;display:flex;align-items:center;justify-content:center;flex:none}
.divider{left:111px;top:322px;width:981px;height:1px;background:rgba(255,255,255,.35)}
.copyright{left:0;top:364px;width:1200px;text-align:center;font-size:15px;font-weight:500}
</style>
</head>
<body>

<header class="hero">
  <svg class="abs" width="1200" height="780" viewBox="0 0 1200 780" style="left:0;top:0">
    <defs>
      <linearGradient id="heroPhoto" x1="0" y1="0" x2="0" y2="1">
        <stop offset="0" stop-color="#e6e9ea"/>
        <stop offset=".45" stop-color="#c9cfcf"/>
        <stop offset=".72" stop-color="#9a8f86"/>
        <stop offset="1" stop-color="#b4583f"/>
      </linearGradient>
    </defs>
    <path role="img" aria-label="Photo of a sprinter launching from starting blocks on a running track" fill="url(#heroPhoto)" d="M0,0 H1200 V470 C950,640 700,730 470,722 C300,716 150,640 0,528 Z"/>
    <path fill="var(--navy)" d="M0,455 C130,650 300,790 470,780 C700,770 930,640 1200,478 L1200,470 C950,626 700,728 470,722 C300,716 150,640 0,528 Z"/>
  </svg>
  <nav class="nav">
    <div class="nav-logo">PeakRoamJourneys</div>
    <div class="nav-links">
      <span class="active">Home</span><span>About</span><span>Sports Travel</span><span>Reviews</span><span>FAQ</span><span>Contact</span>
    </div>
    <div class="nav-quote">Get A Quote</div>
  </nav>
  <h1 class="abs hero-title">Experience the World’s Greatest Sporting Events — In Style.</h1>
  <p class="abs hero-sub">Premier sports travel and event services for discerning fans, corporate groups, and associations.</p>
  <div class="abs btn hero-btn">Explore Experiences</div>
  <div class="abs play"><span><svg width="20" height="22" viewBox="0 0 20 22"><path d="M2 1 L19 11 L2 21 Z" fill="#fff"/></svg></span></div>
</header>

<section>
  <svg class="abs about-visual" width="500" height="410" viewBox="0 0 500 410">
    <defs>
      <linearGradient id="stadium" x1="0" y1="0" x2="0" y2="1">
        <stop offset="0" stop-color="#1d2c56"/>
        <stop offset=".5" stop-color="#6f86a8"/>
        <stop offset=".75" stop-color="#3f7a3b"/>
        <stop offset="1" stop-color="#151515"/>
      </linearGradient>
    </defs>
    <ellipse cx="232" cy="205" rx="235" ry="182" transform="rotate(-30 232 205)" fill="var(--gold)"/>
    <ellipse cx="268" cy="190" rx="232" ry="168" transform="rotate(-30 268 190)" fill="#fff"/>
    <ellipse role="img" aria-label="Photo of cheering fans in a floodlit football stadium" cx="268" cy="180" rx="220" ry="160" transform="rotate(-30 268 180)" fill="url(#stadium)"/>
  </svg>
  <h2 class="abs about-title">About <span class="gold">PeakRoamJourneys</span></h2>
  <div class="abs about-text">
    <p>Lorem ipsum dolor sit amet, consectetur adipiscing elit, sed do eiusmod tempor incididunt ut labore et dolore magna aliqua. Ut enim ad minim veniam, quis nostrud exercitation ullamco laboris nisi ut aliquip ex ea commodo consequat.</p>
    <p>Duis aute irure dolor in reprehenderit in voluptate velit esse cillum dolore eu fugiat nulla pariatur. Excepteur sint occaecat cupidatat non proident, sunt in culpa qui officia deserunt mollit anim id est laborum. Nemo enim ipsam voluptatem quia voluptas sit aspernatur aut odit aut fugit, sed quia consequuntur magni dolores eos qui ratione voluptatem sequi nesciunt.</p>
  </div>
  <div class="abs btn about-btn">Read More</div>
</section>

<section class="abs products">
  <h2 class="section-title">Sports Travel <span class="gold">Products</span></h2>
  <div class="product-card" role="img" aria-label="Photo of a skier on a snowy slope" style="left:-83px;background:linear-gradient(160deg,#e4e4e4,#9a9a9a)"><div class="label" style="justify-content:flex-end;padding-right:82px">Skiing</div></div>
  <div class="product-card" role="img" aria-label="Photo of a flag with ring emblem over a city skyline" style="left:194px;background:linear-gradient(180deg,#7fa8dc,#e8eef5 55%,#8a8a80)"><div class="label">Vantara Games</div></div>
  <div class="product-card" role="img" aria-label="Photo of a golden trophy under stage lights" style="left:470px;background:radial-gradient(circle at 50% 45%,#d9a64a,#7a3b55 45%,#1e1330)"><div class="label">Globe Shield</div></div>
  <div class="product-card" role="img" aria-label="Photo of a tennis racket and ball in a stadium" style="left:746px;background:linear-gradient(180deg,#5a6d86,#7ea1c2 55%,#2f4e75)"><div class="label">Royal Quartet</div></div>
  <div class="product-card" role="img" aria-label="Photo of players contesting a football" style="left:1021px;background:linear-gradient(160deg,#3f5a3a,#8a3a3a 60%,#2c4b2a)"><div class="label" style="justify-content:flex-start;padding-left:85px">Football</div></div>
  <div class="arrow" style="left:38px"><svg width="18" height="14" viewBox="0 0 18 14"><path d="M17 7H2M7 1L1 7l6 6" stroke="#fff" stroke-width="2" fill="none"/></svg></div>
  <div class="arrow" style="left:1127px"><svg width="18" height="14" viewBox="0 0 18 14"><path d="M1 7h15M11 1l6 6-6 6" stroke="#fff" stroke-width="2" fill="none"/></svg></div>
</section>

<section class="abs reviews">
  <h2 class="section-title">What Our <span class="gold">Customer Says</span></h2>
  <article class="review-card" style="left:111px"><div class="avatar" role="img" aria-label="Customer portrait"></div><h3>Daniel Hartwell</h3><div class="stars">★★★★★</div><p>Temporibus autem quibusdam et aut<br>officiis debitis aut rerum necessitatibus<br>saepe eveniet ut et voluptates</p></article>
  <article class="review-card" style="left:451px"><div class="avatar" role="img" aria-label="Customer portrait"></div><h3>Marcus Lowe</h3><div class="stars">★★★★★</div><p>Itaque earum rerum hic tenetur a sapiente<br>delectus, reiciendis voluptatibus maiores<br>alias consequatur aut</p></article>
  <article class="review-card" style="left:789px"><div class="avatar" role="img" aria-label="Customer portrait"></div><h3>Ella Brandt</h3><div class="stars">★★★★★</div><p>Nam libero tempore, cum soluta nobis est<br>eligendi optio cumque nihil impedit quo<br>minus id quod</p></article>
</section>

<section class="abs faq">
  <h2 class="section-title">Frequently <span class="gold">Asked Questions</span></h2>
  <div class="faq-item" style="top:139px">1) Excepteur sint occaecat cupidatat non proident, sunt in culpa qui officia?<span class="plus">+</span></div>
  <div class="faq-item" style="top:216px">2) Excepteur sint occaecat cupidatat non proident, sunt in culpa qui officia?<span class="plus">+</span></div>
  <div class="faq-item" style="top:293px">3) Excepteur sint occaecat cupidatat non proident, sunt in culpa qui officia?<span class="plus">+</span></div>
  <div class="faq-item" style="top:370px">4) Excepteur sint occaecat cupidatat non proident, sunt in culpa qui officia?<span class="plus">+</span></div>
  <div class="faq-item" style="top:447px">5) Excepteur sint occaecat cupidatat non proident, sunt in culpa qui officia?<span class="plus">+</span></div>
  <div class="abs btn faq-btn">View More</div>
</section>

<section class="abs contact">
  <h2 class="section-title">Get In <span class="gold">Touch With Us</span></h2>
  <div class="field" style="left:111px;top:124px;width:479px;height:59px">Name</div>
  <div class="field" style="left:608px;top:124px;width:479px;height:59px">Email</div>
  <div class="field" style="left:111px;top:199px;width:479px;height:59px">Phone Number</div>
  <div class="field" style="left:608px;top:199px;width:479px;height:59px">Address</div>
  <div class="field" style="left:111px;top:272px;width:976px;height:217px">Message</div>
  <div class="abs btn submit-btn">Submit</div>
</section>

<footer class="abs footer">
  <div class="abs footer-logo">PeakRoamJourneys</div>
  <span class="social on" style="left:111px"></span>
  <span class="social" style="left:157px"></span>
  <span class="social" style="left:203px"></span>
  <span class="social" style="left:248px"></span>

  <h4 style="left:441px">Quick Links</h4>
  <ul style="left:441px">
    <li>➜ Home</li><li>➜ About</li><li>➜ Products</li><li>➜ Reviews</li><li>➜ Contact Us</li>
  </ul>
  <h4 style="left:640px">Help Links</h4>
  <ul style="left:640px">
    <li>➜ FAQ</li><li>➜ Terms of use</li><li>➜ Privacy Policy</li><li>➜ Support Links</li><li>➜ Conditions</li>
  </ul>
  <h4 style="left:828px">Contact Us</h4>
  <div class="contact-row" style="top:120px"><span class="ico"><svg width="14" height="18" viewBox="0 0 14 18"><path d="M7 0a7 7 0 0 0-7 7c0 5 7 11 7 11s7-6 7-11a7 7 0 0 0-7-7zm0 9.5A2.5 2.5 0 1 1 7 4.5a2.5 2.5 0 0 1 0 5z" fill="var(--navy)"/></svg></span><span>PeakRoamJourneys<br>United States</span></div>
  <div class="contact-row" style="top:188px;align-items:center"><span class="ico"><svg width="16" height="16" viewBox="0 0 16 16"><path d="M3.5 1l3 3-2 2a9 9 0 0 0 5.5 5.5l2-2 3 3-2 2.5C7 15 1 9 1 3z" fill="var(--navy)"/></svg></span><span>+1 555 010 2040</span></div>
  <div class="contact-row" style="top:240px;align-items:center"><span class="ico"><svg width="16" height="12" viewBox="0 0 16 12"><rect width="16" height="12" rx="2" fill="var(--navy)"/><path d="M1 1l7 6 7-6" stroke="#fff" stroke-width="1.5" fill="none"/></svg></span><span>info@peakroamjourneys.example</span></div>

  <div class="abs divider"></div>
  <div class="abs copyright">Copyrights@2025.PeakRoamJourneys.All Rights Reserved</div>
</footer>

</body>
</html>
```